Need a clean & modern homepage for an education site + opportunity for longer term work

Thanks for viewing our project. We are excited about this new website and we hope that we might build a relationship with designers as we work on this project. I provided quite a few details and requirements to help you more quickly create a design that meets our needs.
Who we are:
We are a website that discusses the importance of college accreditation and provides a directory of college programs.
What we need:
A homepage that meets the below requirements and is inspired by the examples provided
Definition of accredited:
ac·cred·it·ed [uh-kred-i-tid] adj.
1. officially recognized as meeting the essential requirements, as of academic excellence: accredited schools.
2. provided with official credentials, as by a government: an accredited diplomatic representative.
3. accepted as authoritative: an accredited theory.
Overall look and feel for the homepage:
- Clean, simple and modern
- Limited (or zero) pictures
- Utilize color blocks with text
- A trend seems to be longer vertical length homepages with lots of whitespace. I generally like this trend as long as the page is not way to tall.
Inspirations: Sites that have a similar look and feel to what I need.
http://lernvoxa.org/
http://www.campusmetrik.com/colleges/brantmoor-university/
http://quietfolding.org/
http://www.velostrahiring.com/
http://www.zunq.com/
http://sketches.bxv.com/
Items to be included on the homepage. Details below on each item.
- Top navigation
- Logo: Please leave a blank area for a logo. The logo has not been designed.
- Simple graphic/color block at the top that highlights a definition of “Accredited” – the definition should be formatted like it is being copy/pasted from a dictionary.
- Space for a video and small (50 word) written description of the video. You can use placeholder text.
- One section with 3 Paragraphs of content (each paragraph around 100 words) with a header at the top. You can use placeholder text but please create the formatting. At the end of the 3 paragraphs please have a “Read More” Note this shouldn't be 3 separate paragraphs with three read mores - it is 3 paragraphs with one read more at the end.
- An area with the header “Search Colleges by State” that has anchor text links to all 50 states.
Top navigation:
- Home
- States – with a subnav dropdown that includes all 50 US states.
- Programs – with a subnav dropdown that includes program titles (list below)
- Degrees - with a subnav dropdown that includes 5 degree levels (list below)
- Accreditation – no subnav
- Rankings – no subnav
- Resources – no subnav
Footer
- Link to about us, privacy, and a copyright www.url.com
Programs List for sub navigation
Accounting
Art
Bible
Business
Criminal Justice
Design
Education
Engineering
English
Law
LPN to RN
Management
Math
MBA
MPH
Medical Assisting
Military
Nursing
Occupational Therapy
Paralegal
Psychology
Pharmacy
RN to BSN
Radiology
Social Work
Sonography
Degrees list for sub navigation
Certificate
Associate
Bachelors
Masters
PhD
Thanks so much - looking forward to working with you!
Education

```html
<!DOCTYPE html>
<html lang="en">
<head>
<meta charset="utf-8">
<title>Accredited Colleges – Home</title>
<link rel="stylesheet" href="https://fonts.googleapis.com/css2?family=Questrial&family=Montserrat:wght@400;600;700&display=swap">
<style>
:root{
  --top-blue:#1e9fe0;
  --ink:#1d2c5a;
  --nav:#8a8f99;
  --green:#4cba62;
  --cyan:#2fb8dc;
  --cyan-dark:#25a6cb;
  --mid-blue:#1c80c2;
  --deep-blue:#1467a6;
  --state-btn:#5f9ccc;
  --card-btn:#63c8ef;
  --paper:#f3f3f3;
  --white:#ffffff;
  --body:#555b63;
}
*{margin:0;padding:0;box-sizing:border-box}
html,body{width:1200px;height:2462px;overflow:hidden;background:var(--white)}
body{position:relative;font-family:"Questrial",sans-serif;color:var(--body)}
.abs{position:absolute}

/* header */
.site-header{left:0;top:0;width:1200px;height:91px;background:var(--white);border-top:8px solid var(--top-blue)}
.brand{left:104px;top:32px;font-family:"Montserrat",sans-serif;font-weight:600;font-size:21px;color:var(--ink)}
.nav{left:0;top:46px;font-size:18px;color:var(--nav)}
.nav span{position:absolute;white-space:nowrap}
.social{left:880px;top:14px;display:flex;gap:15px}
.social i{display:block;width:24px;height:24px;border-radius:50%;background:var(--green)}

/* hero */
.hero{left:0;top:91px;width:1200px;height:439px;background:linear-gradient(180deg,#a8d6ee 0%,#86b8d2 100%)}
.definition{left:21px;top:152px;width:623px;height:160px;background:rgba(60,160,210,.85);padding:18px 20px;color:var(--white);font-family:"Montserrat",sans-serif;font-weight:700;font-size:21px;line-height:27px;text-transform:uppercase}
.search-bar{left:152px;top:421px;width:793px;height:77px;background:rgba(70,150,190,.55)}
.search-bar .field{position:absolute;top:19px;height:40px;background:var(--white);border-radius:3px;font-size:17px;color:#8d8d8d;padding:10px 20px}
.search-bar .btn{position:absolute;left:647px;top:19px;width:114px;height:40px;background:#1ea2e4;color:var(--white);font-family:"Montserrat",sans-serif;font-weight:600;font-size:17px;text-align:center;line-height:40px}

/* video band */
.video-band{left:0;top:530px;width:1200px;height:200px}
.video-text{left:208px;top:554px;width:420px;font-size:16.5px;line-height:17.5px;color:var(--white)}
.watch{left:405px;top:650px;width:155px;height:38px;border:2px solid var(--white);color:var(--white);font-size:20px;text-align:center;line-height:34px}
.video-thumb{left:716px;top:544px;width:237px;height:154px;background:linear-gradient(135deg,#dfe8ee,#a9c7dc);border:3px solid var(--white)}

/* feature cards */
.features{left:0;top:716px;width:1200px;height:408px;background:var(--paper)}
.card{width:313px;height:292px;background:var(--white);top:764px}
.card .icon{position:absolute;left:14px;top:20px}
.card h3{position:absolute;left:110px;top:38px;font-family:"Montserrat",sans-serif;font-weight:600;font-size:20px;color:#555}
.card .sub{position:absolute;left:110px;top:62px;font-size:22px;color:#777}
.card p{position:absolute;left:18px;top:112px;width:280px;height:122px;overflow:hidden;font-size:12.5px;line-height:15.5px;color:#666;text-align:justify}
.card .more{position:absolute;left:0;top:255px;width:313px;height:37px;background:var(--card-btn);color:var(--white);font-size:20px;text-align:center;line-height:37px}
.card .more.active{background:var(--green)}

/* about section */
.about{left:0;top:1121px;width:1200px;height:706px;background:var(--cyan)}
.about-title{left:158px;top:1186px;font-family:"Montserrat",sans-serif;font-weight:600;font-size:35px;color:var(--white)}
.row h4{position:absolute;left:295px;font-family:"Montserrat",sans-serif;font-weight:600;font-size:24px;color:var(--white)}
.row p{position:absolute;left:295px;width:805px;font-size:15px;line-height:16.5px;color:var(--white);text-align:justify}
.read-more{left:758px;top:1771px;width:334px;height:56px;background:var(--cyan-dark);color:var(--white);font-size:50px;text-align:center;line-height:56px}

/* directory */
.directory{left:0;top:1827px;width:1200px;height:295px;background:var(--mid-blue)}
.dir-head{font-family:"Montserrat",sans-serif;font-weight:600;font-size:24px;color:var(--white);top:1872px}
.list{top:1919px;font-size:16px;line-height:18.6px;color:var(--white);list-style:none}
.divider{top:1920px;width:2px;height:150px;background:rgba(255,255,255,.75)}

/* states */
.states{left:0;top:2122px;width:1200px;height:245px;background:var(--deep-blue)}
.states-head{left:93px;top:2146px;font-family:"Montserrat",sans-serif;font-weight:600;font-size:24px;color:var(--white);display:flex;align-items:center;gap:8px}
.state-grid{left:91px;top:2205px;display:grid;grid-template-columns:repeat(5,120px);column-gap:7px;row-gap:14px}
.state-grid span{height:24px;background:var(--state-btn);color:var(--white);font-size:14px;text-align:center;line-height:24px}
.us-map{left:754px;top:2173px;width:346px;height:173px;background:linear-gradient(135deg,#8fb8dc,#5d96c8);border-radius:6px}

/* footer */
.site-footer{left:0;top:2367px;width:1200px;height:95px;background:var(--green);color:var(--white);font-size:27px}
.site-footer span{position:absolute;top:30px}
</style>
</head>
<body>

<header class="site-header abs">
  <div class="brand abs">MY WEBSITE B\NAME</div>
  <nav class="nav abs">
    <span style="left:424px">Home</span>
    <span style="left:498px">States</span>
    <span style="left:570px">Programs</span>
    <span style="left:669px">Degrees</span>
    <span style="left:768px">Accreditation</span>
    <span style="left:892px">Rankings</span>
    <span style="left:989px">Resources</span>
  </nav>
  <div class="social abs"><i></i><i></i><i></i><i></i></div>
</header>

<section class="hero abs" role="img" aria-label="Hero photo: road leading toward signs reading Learning and Education"></section>
<div class="definition abs">Simple graphic/color block at the top that highlights a definition of “accredited” – the definition should be formatted like it is being copy/pasted from a dictionary.</div>
<form class="search-bar abs">
  <div class="field" style="left:14px;width:409px">Search Collage</div>
  <div class="field" style="left:438px;width:191px">State
    <svg style="position:absolute;right:14px;top:12px" width="12" height="16" viewBox="0 0 12 16"><path d="M6 1a5 5 0 0 0-5 5c0 4 5 9 5 9s5-5 5-9a5 5 0 0 0-5-5z" fill="none" stroke="#999" stroke-width="1.5"/><circle cx="6" cy="6" r="1.8" fill="#999"/></svg>
  </div>
  <div class="btn">SEARCH</div>
</form>

<svg class="video-band abs" width="1200" height="200" viewBox="0 0 1200 200" aria-hidden="true">
  <path d="M0 0H1200V172Q600 200 0 172Z" fill="var(--green)"/>
</svg>
<p class="video-text abs">written description of the videowritten description of the videowritten description of the video written description of the video written description of the video written description of the video written description of the video</p>
<div class="watch abs">Watch video</div>
<svg class="abs" style="left:586px;top:640px" width="105" height="52" viewBox="0 0 105 52" aria-hidden="true">
  <path d="M2 22Q20 52 60 38L98 14" fill="none" stroke="#fff" stroke-width="2.5"/>
  <path d="M80 8L100 12L92 32" fill="none" stroke="#fff" stroke-width="2.5"/>
</svg>
<div class="video-thumb abs" role="img" aria-label="Video preview of a student"></div>
<svg class="abs" style="left:806px;top:597px" width="50" height="50" viewBox="0 0 50 50" aria-hidden="true">
  <circle cx="25" cy="25" r="23" fill="#3aa0dc" stroke="#fff" stroke-width="3"/>
  <path d="M19 14L36 25L19 36Z" fill="#fff"/>
</svg>

<section class="features abs"></section>
<article class="card abs" style="left:93px">
  <svg class="icon" width="76" height="76" viewBox="0 0 76 76" aria-hidden="true"><circle cx="38" cy="38" r="35" fill="none" stroke="#444" stroke-width="4"/><path d="M16 28L38 18L60 28L38 38Z" fill="#444"/><circle cx="38" cy="46" r="11" fill="none" stroke="#444" stroke-width="3"/></svg>
  <h3>Rankingsp</h3><div class="sub">explain small-desc</div>
  <p>One section with 3 Paragraphs of content (each paragraph around 100 words) with a header at the top. You can use placeholder text but please create the formatting. At the end of the 3 paragraphs please have a “Read More” Note this shouldn't be 3 separate paragraphs with three read mores - it is 3 paragraphs with one read more at the end.One section with 3 Paragraphs of content (each</p>
  <div class="more active">Read More</div>
</article>
<article class="card abs" style="left:428px">
  <svg class="icon" width="76" height="76" viewBox="0 0 76 76" aria-hidden="true"><circle cx="38" cy="38" r="35" fill="none" stroke="#444" stroke-width="4"/><circle cx="38" cy="34" r="15" fill="none" stroke="#444" stroke-width="3"/><path d="M23 34H53M38 19V49M30 58H46M38 49V58" stroke="#444" stroke-width="3"/></svg>
  <h3>Accreditation</h3><div class="sub">explain small-desc</div>
  <p>One section with 3 Paragraphs of content (each paragraph around 100 words) with a header at the top. You can use placeholder text but please create the formatting. At the end of the 3 paragraphs please have a “Read More” Note this shouldn't be 3 separate paragraphs with three read mores - it is 3 paragraphs with one read more at the end.One section with 3 Paragraphs of content (each</p>
  <div class="more">Read More</div>
</article>
<article class="card abs" style="left:766px">
  <svg class="icon" width="76" height="76" viewBox="0 0 76 76" aria-hidden="true"><circle cx="38" cy="38" r="35" fill="none" stroke="#444" stroke-width="4"/><rect x="20" y="22" width="34" height="9" rx="2" fill="#444"/><rect x="24" y="34" width="32" height="9" rx="2" fill="#444"/><rect x="20" y="46" width="36" height="9" rx="2" fill="#444"/></svg>
  <h3>Resources</h3><div class="sub">explain small-desc</div>
  <p>One section with 3 Paragraphs of content (each paragraph around 100 words) with a header at the top. You can use placeholder text but please create the formatting. At the end of the 3 paragraphs please have a “Read More” Note this shouldn't be 3 separate paragraphs with three read mores - it is 3 paragraphs with one read more at the end.One section with 3 Paragraphs of content (each</p>
  <div class="more">Read More</div>
</article>

<section class="about abs"></section>
<svg class="abs" style="left:0;top:1116px" width="1200" height="60" viewBox="0 0 1200 60" aria-hidden="true">
  <rect x="0" y="5" width="1200" height="55" fill="var(--cyan)"/>
  <path d="M0 0H508Q540 0 560 22L577 40L594 22Q614 0 646 0H1200V5H0Z" fill="var(--paper)"/>
  <path d="M567 22H587M577 12V32" stroke="#666" stroke-width="4"/>
</svg>
<h2 class="about-title abs">header at the top</h2>

<div class="row">
  <svg class="abs" style="left:135px;top:1268px" width="135" height="115" viewBox="0 0 135 115" aria-hidden="true"><path d="M4 40L68 8L132 40L68 72Z" fill="#fff"/><path d="M34 58V92Q68 112 102 92V58L68 76Z" fill="#fff"/><rect x="14" y="42" width="5" height="50" fill="#fff"/></svg>
  <h4 style="top:1276px">header at the top</h4>
  <p style="top:1308px">One section with 3 Paragraphs of content (each paragraph around 100 words) with a header at the top. You can use placeholder text but please create the formatting. At the end of the 3 paragraphs please have a “Read More” Note this shouldn't be 3 separate paragraphs with three read mores - it is 3 paragraphs with one read more at the end.One section with 3 Paragraphs of content (each paragraph around 100 words) with a header at the top. You can use placeholder text but please create the formatting. At the end of the 3 paragraphs please have a “Read More” Note this shouldn't be 3 separate paragraphs with three read mores - it is 3 paragraphs with one read more at</p>
</div>
<div class="row">
  <svg class="abs" style="left:140px;top:1450px" width="125" height="130" viewBox="0 0 125 130" aria-hidden="true"><rect x="8" y="6" width="60" height="48" fill="none" stroke="#fff" stroke-width="5"/><circle cx="90" cy="16" r="10" fill="#fff"/><path d="M80 30H100V66H80Z" fill="#fff"/><path d="M68 40L82 34" stroke="#fff" stroke-width="5"/><circle cx="20" cy="92" r="9" fill="#fff"/><circle cx="62" cy="92" r="9" fill="#fff"/><circle cx="104" cy="92" r="9" fill="#fff"/><path d="M6 126Q20 100 34 126ZM48 126Q62 100 76 126ZM90 126Q104 100 118 126Z" fill="#fff"/></svg>
  <h4 style="top:1447px">header at the top</h4>
  <p style="top:1480px">One section with 3 Paragraphs of content (each paragraph around 100 words) with a header at the top. You can use placeholder text but please create the formatting. At the end of the 3 paragraphs please have a “Read More” Note this shouldn't be 3 separate paragraphs with three read mores - it is 3 paragraphs with one read more at the end.One section with 3 Paragraphs of content (each paragraph around 100 words) with a header at the top. You can use placeholder text but please create the formatting. At the end of the 3 paragraphs please have a “Read More” Note this shouldn't be 3 separate paragraphs with three read mores - it is 3 paragraphs with one read more at</p>
</div>
<div class="row">
  <svg class="abs" style="left:122px;top:1615px" width="140" height="110" viewBox="0 0 140 110" aria-hidden="true"><path d="M4 40L70 6L136 40L70 74Z" fill="#fff"/><path d="M30 56V82Q70 100 110 82V56L70 78Z" fill="#fff"/><path d="M36 60V106L46 96L56 106V66Z" fill="#fff" stroke="var(--cyan)" stroke-width="2"/></svg>
  <h4 style="top:1614px">header at the top</h4>
  <p style="top:1646px">One section with 3 Paragraphs of content (each paragraph around 100 words) with a header at the top. You can use placeholder text but please create the formatting. At the end of the 3 paragraphs please have a “Read More” Note this shouldn't be 3 separate paragraphs with three read mores - it is 3 paragraphs with one read more at the end.One section with 3 Paragraphs of content (each paragraph around 100 words) with a header at the top. You can use placeholder text but please create the formatting. At the end of the 3 paragraphs please have a “Read More” Note this shouldn't be 3 separate paragraphs with three read mores - it is 3 paragraphs with one read more at</p>
</div>
<div class="read-more abs">Read More</div>

<section class="directory abs"></section>
<svg class="abs" style="left:560px;top:1827px" width="34" height="22" viewBox="0 0 34 22" aria-hidden="true"><path d="M2 2H32L17 20Z" fill="#fff"/></svg>
<h3 class="dir-head abs" style="left:112px">Programs</h3>
<h3 class="dir-head abs" style="left:683px;top:1876px">Degrees</h3>
<ul class="list abs" style="left:118px"><li>Accounting</li><li>Art</li><li>Bible</li><li>Business</li><li>Criminal Justice</li><li>Design</li><li>Education</li><li>Engineering</li><li>English</li></ul>
<div class="divider abs" style="left:283px"></div>
<ul class="list abs" style="left:322px;top:1921px"><li>Accounting</li><li>Art</li><li>Bible</li><li>Business</li><li>Criminal Justice</li><li>Design</li><li>Education</li><li>Engineering</li><li>English</li></ul>
<div class="divider abs" style="left:467px"></div>
<ul class="list abs" style="left:505px;top:1928px"><li>Accounting</li><li>Art</li><li>Bible</li><li>Business</li><li>Criminal Justice</li><li>Design</li><li>Education</li><li>Engineering</li><li>English</li></ul>
<div class="divider abs" style="left:650px"></div>
<ul class="list abs" style="left:687px;top:1928px"><li>Accounting</li><li>Art</li><li>Bible</li><li>Business</li><li>Criminal Justice</li><li>Design</li><li>Education</li><li>Engineering</li><li>English</li></ul>
<div class="divider abs" style="left:834px"></div>
<ul class="list abs" style="left:872px;top:1928px"><li>Accounting</li><li>Art</li><li>Bible</li><li>Business</li><li>Criminal Justice</li><li>Design</li><li>Education</li><li>Engineering</li><li>English</li></ul>

<section class="states abs"></section>
<h3 class="states-head abs">
  <svg width="22" height="22" viewBox="0 0 22 22" aria-hidden="true"><circle cx="9" cy="9" r="6.5" fill="none" stroke="#fff" stroke-width="3"/><path d="M14 14L20 20" stroke="#fff" stroke-width="3.5"/></svg>
  Colleges by State
</h3>
<nav class="state-grid abs">
  <span>state</span><span>state</span><span>state</span><span>state</span><span>state</span>
  <span>state</span><span>state</span><span>state</span><span>state</span><span>state</span>
  <span>state</span><span>state</span><span>state</span><span>state</span><span>state</span>
  <span>state</span><span>state</span><span>state</span><span>state</span><span>state</span>
</nav>
<div class="us-map abs" role="img" aria-label="Map of the United States with clickable states"></div>

<footer class="site-footer abs">
  <span style="left:77px">copyright@www.url.com</span>
  <span style="left:789px">about us</span>
  <span style="left:930px">privacy</span>
</footer>

</body>
</html>
```